Business Card design for law firm = Brightvale Australia

We are seeking a new design for our business cards.
We are keeping our logo, which is attached.
We need space for
Name
Title
Address is , which is
Level 7
214 Marlowe Street
Sydney NSW 2047
Phone :
Mobile :
Fax :
Email :
DX :
website www.brightvale-example.com.au

Industry/Entity Type

Law Firm / Banking and Finance

Contact Information for Business Card

We are seeking a new design for our business cards. We are keeping our logo. We need space for Name Title Address is Level 7 214 Marlowe Street Sydney NSW 2047 Phone Mobile Fax Email DX website www.brightvale-example.com.au

Colors
0054AA
0677BA
7BADD7
CADEEF
E8F1F8

Requirements
Must have
• see our website for general feel www.brightvale-example.com.au

```html
<!DOCTYPE html>
<html lang="en">
<head>
<meta charset="utf-8">
<title>Brightvale Australia — Business Cards</title>
<link href="https://fonts.googleapis.com/css2?family=Crimson+Pro:wght@500&family=Montserrat:wght@400&display=swap" rel="stylesheet">
<style>
  :root {
    --backdrop: #adadad;
    --card: #ffffff;
    --brand-navy: #0a3fb0;
    --brand-blue: #0a8bd0;
    --text-grey: #555555;
  }
  html, body {
    margin: 0;
    padding: 0;
    width: 1200px;
    height: 1056px;
    overflow: hidden;
    background: var(--backdrop);
  }
  .stage {
    position: relative;
    width: 1200px;
    height: 1056px;
  }
  .card {
    position: absolute;
    left: 280px;
    width: 640px;
    height: 366px;
    background: var(--card);
    box-shadow: 0 14px 30px rgba(0,0,0,0.22);
    overflow: hidden;
  }
  .card--contact { top: 110px; }
  .card--brand { top: 540px; }

  /* Contact side */
  .contact-list {
    position: absolute;
    left: 46px;
    top: 36px;
    margin: 0;
    padding: 0;
    list-style: none;
    font-family: "Montserrat", sans-serif;
    font-size: 16px;
    line-height: 27px;
    color: var(--text-grey);
  }
  .contact-list li {
    display: flex;
    align-items: center;
    gap: 8px;
  }
  .contact-list svg, .address svg {
    width: 14px;
    height: 14px;
    fill: var(--brand-navy);
    flex: none;
  }
  .accent-block {
    position: absolute;
    background: var(--brand-blue);
  }
  .card--contact .accent-block {
    right: 62px;
    top: 36px;
    width: 172px;
    height: 140px;
  }
  .person {
    position: absolute;
    right: 58px;
    top: 188px;
    text-align: right;
  }
  .person-name {
    margin: 0;
    font-family: "Crimson Pro", serif;
    font-weight: 500;
    font-size: 40px;
    line-height: 1;
    color: var(--brand-navy);
  }
  .person-title {
    margin: 6px 0 0;
    font-family: "Montserrat", sans-serif;
    font-size: 17px;
    color: var(--text-grey);
  }
  .address {
    position: absolute;
    right: 78px;
    bottom: 26px;
    margin: 0;
    font-family: "Montserrat", sans-serif;
    font-style: normal;
    font-size: 16px;
    line-height: 23px;
    color: var(--text-grey);
    text-align: right;
  }
  .address .line-with-pin {
    position: relative;
  }
  .address .line-with-pin svg {
    position: absolute;
    right: -20px;
    top: 3px;
  }
  .wordmark {
    position: absolute;
    margin: 0;
    font-family: "Crimson Pro", serif;
    font-weight: 500;
    color: var(--brand-navy);
    line-height: 1;
  }
  .card--contact .wordmark {
    left: 50px;
    bottom: 52px;
    font-size: 44px;
  }

  /* Brand side */
  .card--brand .accent-block--top {
    left: 0;
    top: 0;
    width: 140px;
    height: 140px;
  }
  .card--brand .accent-block--bottom {
    right: 0;
    bottom: 40px;
    width: 140px;
    height: 136px;
  }
  .card--brand .wordmark {
    left: 0;
    right: 0;
    top: 150px;
    text-align: center;
    font-size: 64px;
  }
</style>
</head>
<body>
<main class="stage">

  <section class="card card--contact" aria-label="Business card, contact side">
    <ul class="contact-list">
      <li>
        <svg viewBox="0 0 16 16" aria-hidden="true"><path d="M2 6c0-2 2-4 6-4s6 2 6 4v1h-3V5.5C10 5 9 4.8 8 4.8S6 5 5 5.5V7H2zM4 8h8l2 6H2z"/></svg>
        +61-400-555-210
      </li>
      <li>
        <svg viewBox="0 0 16 16" aria-hidden="true"><path d="M3 1l3 0 1 4-2 1.5c1 2 2.5 3.5 4.5 4.5L11 9l4 1v3c0 1-1 2-2 2C7 15 1 9 1 3c0-1 1-2 2-2z"/></svg>
        +61-2-5550-1834
      </li>
      <li>
        <svg viewBox="0 0 16 16" aria-hidden="true"><path d="M4 1h8v4H4zM1 6h14v7h-2v2H3v-2H1zM4 10v4h8v-4z"/></svg>
        +61-2-5550-1835
      </li>
      <li>
        <svg viewBox="0 0 16 16" aria-hidden="true"><path d="M1 3h14v10H1zM2 4.2v.6l6 4.2 6-4.2v-.6L8 8z"/></svg>
        hello@brightvale-example.com.au
      </li>
      <li>
        <svg viewBox="0 0 16 16" aria-hidden="true"><path d="M8 1a7 7 0 1 0 0 14A7 7 0 0 0 8 1zm0 1.5c.8 0 1.8 1.8 2 4.5H6c.2-2.7 1.2-4.5 2-4.5zM2.6 7h2.4c0-1.6.4-3 1-4A5.6 5.6 0 0 0 2.6 7zm8.4 0h2.4A5.6 5.6 0 0 0 10 3c.6 1 1 2.4 1 4zM2.6 9A5.6 5.6 0 0 0 6 13c-.6-1-1-2.4-1-4zm3.4 0c.2 2.7 1.2 4.5 2 4.5s1.8-1.8 2-4.5zm5 0c0 1.6-.4 3-1 4a5.6 5.6 0 0 0 3.4-4z"/></svg>
        www.brightvale-example.com.au
      </li>
    </ul>

    <div class="accent-block"></div>

    <div class="person">
      <p class="person-name">Mara Quill</p>
      <p class="person-title">Director / CEO</p>
    </div>

    <address class="address">
      <span class="line-with-pin">Level 7<svg viewBox="0 0 16 16" aria-hidden="true"><path d="M8 1a5 5 0 0 0-5 5c0 4 5 9 5 9s5-5 5-9a5 5 0 0 0-5-5zm0 3a2 2 0 1 1 0 4 2 2 0 0 1 0-4z"/></svg></span><br>
      214 Marlowe Street<br>
      Sydney NSW 2047
    </address>

    <p class="wordmark">Brightvale</p>
  </section>

  <section class="card card--brand" aria-label="Business card, brand side">
    <div class="accent-block accent-block--top"></div>
    <p class="wordmark">Brightvale</p>
    <div class="accent-block accent-block--bottom"></div>
  </section>

</main>
</body>
</html>
```